RWT Fittings Ltd Business Cards

We need a business card with our business logo. We provide window and door installations on high-rises in west coast British Colombia, Canada.

I would like my business information and details on one side of the card, and the other side the company name with logo

Target Market(s)

General Contractors

Industry/Entity Type

Construction

Contact Information for Business Card

one side i want my company name and logo in the dark theme logo that i provided

Requirements
Must have
• Marco Peltieri, 16045518293, RWTFittings@mailbox-demo.com, 1407-5194 Linden Row Burnaby BC, V5H 2K9, Owner & Manager

```html
<!DOCTYPE html>
<html lang="en">
<head>
<meta charset="utf-8">
<title>RWT Fittings Ltd – Business Cards</title>
<link href="https://fonts.googleapis.com/css2?family=Open+Sans:wght@400;600;700&display=swap" rel="stylesheet">
<style>
  :root {
    --backdrop: #232323;
    --card: #151515;
    --blue: #29abe2;
    --white: #f4f4f4;
    --grey: #9a9a9a;
    --embossed: #3b3b3b;
  }
  * { box-sizing: border-box; margin: 0; padding: 0; }
  html, body {
    width: 1200px; height: 780px; overflow: hidden;
    background: var(--backdrop);
    font-family: "Open Sans", Arial, sans-serif;
  }
  .canvas { position: relative; width: 1200px; height: 780px; }
  .card {
    position: absolute;
    width: 630px; height: 360px;
    background: var(--card);
    border-radius: 28px;
    box-shadow: -3px 4px 0 var(--blue), 0 18px 30px rgba(0,0,0,.55);
    overflow: hidden;
  }
  .card--back { left: 70px; top: 24px; }
  .card--front { left: 500px; top: 396px; }

  /* back: company name */
  .back-mark {
    position: absolute; inset: 0;
    display: flex; align-items: center; justify-content: center; gap: 18px;
  }
  .back-mark .square { width: 46px; height: 46px; background: var(--embossed); }
  .back-mark .company {
    font-weight: 700; font-size: 46px; letter-spacing: 3px;
    text-transform: uppercase; color: var(--embossed);
  }

  /* front: brand panel on the right */
  .brand-panel {
    position: absolute; right: 0; top: 0;
    width: 300px; height: 360px;
  }

  /* front: details */
  .brand {
    position: absolute; left: 48px; top: 40px;
    display: flex; align-items: center; gap: 12px;
  }
  .brand .square { width: 26px; height: 26px; background: var(--blue); }
  .brand .company {
    font-weight: 700; font-size: 27px; letter-spacing: 1px;
    text-transform: uppercase; color: var(--blue);
  }
  .accent-bar {
    position: absolute; left: 0; top: 118px;
    width: 14px; height: 58px; background: var(--blue);
  }
  .person { position: absolute; left: 48px; top: 116px; }
  .person .name {
    font-weight: 700; font-size: 27px; color: var(--blue);
    text-transform: uppercase; line-height: 1.1;
  }
  .person .role { font-size: 17px; color: var(--white); margin-top: 2px; }
  .address {
    position: absolute; left: 48px; top: 196px;
    font-size: 15px; line-height: 1.4; color: var(--white);
  }
  .contact {
    position: absolute; left: 48px; top: 256px;
    list-style: none; font-size: 15px; color: var(--white);
  }
  .contact li { display: flex; align-items: center; gap: 8px; line-height: 1.6; }
  .contact svg { width: 14px; height: 14px; fill: var(--blue); flex: none; }
</style>
</head>
<body>
<main class="canvas">

  <section class="card card--back" aria-label="Card back">
    <div class="back-mark">
      <span class="square"></span>
      <span class="company">RWT Fittings Ltd</span>
    </div>
  </section>

  <section class="card card--front" aria-label="Card front">
    <svg class="brand-panel" viewBox="0 0 300 360" role="img" aria-label="Decorative brand panel in grey and blue">
      <defs>
        <linearGradient id="panelTone" x1="0" y1="1" x2="1" y2="0">
          <stop offset="0" stop-color="#9a9a9a"/>
          <stop offset="1" stop-color="#29abe2"/>
        </linearGradient>
      </defs>
      <polygon points="170,0 300,0 300,360 40,360" fill="url(#panelTone)"/>
    </svg>

    <div class="brand">
      <span class="square"></span>
      <span class="company">RWT Fittings Ltd</span>
    </div>

    <span class="accent-bar"></span>
    <div class="person">
      <p class="name">Marco Peltieri</p>
      <p class="role">Owner &amp; Manager</p>
    </div>

    <p class="address">1407-5194 Linden Row<br>Burnaby BC, V5H 2K9</p>

    <ul class="contact">
      <li>
        <svg viewBox="0 0 24 24" aria-hidden="true"><path d="M6.6 10.8a15.1 15.1 0 0 0 6.6 6.6l2.2-2.2a1 1 0 0 1 1-.25 11.4 11.4 0 0 0 3.6.57 1 1 0 0 1 1 1V20a1 1 0 0 1-1 1A17 17 0 0 1 3 4a1 1 0 0 1 1-1h3.5a1 1 0 0 1 1 1c0 1.25.2 2.45.57 3.57a1 1 0 0 1-.25 1z"/></svg>
        16045518293
      </li>
      <li>
        <svg viewBox="0 0 24 24" aria-hidden="true"><path d="M2 5h20v14H2z M2 5l10 8 10-8"/></svg>
        RWTFittings@mailbox-demo.com
      </li>
      <li>
        <svg viewBox="0 0 24 24" aria-hidden="true"><circle cx="12" cy="12" r="10"/></svg>
        www.rwtfittings-demo.com
      </li>
    </ul>
  </section>

</main>
</body>
</html>
```